Brightfen Business Card Redesign & Logo Update

We need to update our business cards to something more modern and fresh. Brightfen can provide the current color schemes and old design examples, but welcome creativity in helping us with this redesign. PLEASE NOTE that we no longer utilize the "tree" and/or "leaf" imagery in our branding. If able would apprecaite an update on the quality of our "words only" logo in Ai. / PNG formats too.

Target Market(s)

Investors, landowners, corporate partners, contractors

Industry/Entity Type

Environmental Restoration & Conservation

Contact Information for Business Card

Logo, persons name, title, mailing address, phone and email, website url

Font styles to use
Other font styles liked:
• Merriweather

Requirements
Nice to have
• Logo, persons name, title, mailing address, phone and email, website url, but open to ideams
Should not have
• No all back backgrounds

```html
<!DOCTYPE html>
<html lang="en">
<head>
<meta charset="utf-8">
<title>Brightfen Business Cards</title>
<link rel="stylesheet" href="https://fonts.googleapis.com/css2?family=Open+Sans:wght@400;600;700;800&display=swap">
<style>
  :root {
    --stage: #e9eaec;
    --card-base: #27402f;
    --card-base-light: #335440;
    --brand-orange: #ec7d23;
    --brand-green: #1c9a48;
    --text-light: #ffffff;
  }
  * { margin: 0; padding: 0; box-sizing: border-box; }
  html, body { width: 1200px; height: 780px; overflow: hidden; }
  body {
    background: var(--stage);
    font-family: "Open Sans", Arial, sans-serif;
    position: relative;
  }
  .card {
    position: absolute;
    top: 235px;
    width: 540px;
    height: 310px;
    background: linear-gradient(135deg, var(--card-base-light), var(--card-base));
    overflow: hidden;
    box-shadow: 0 10px 24px rgba(0,0,0,0.25);
  }
  .card--front { left: 40px; }
  .card--back { left: 620px; }

  .card__swoosh { position: absolute; inset: 0; width: 100%; height: 100%; }

  .wordmark {
    position: absolute;
    font-weight: 800;
    color: var(--brand-orange);
    text-transform: uppercase;
    letter-spacing: 1px;
    line-height: 1;
  }
  .card--front .wordmark { top: 40px; right: 40px; font-size: 42px; }
  .card--back .wordmark { top: 100px; left: 0; right: 0; text-align: center; font-size: 62px; }

  .person { position: absolute; left: 58px; top: 122px; width: 200px; text-align: right; }
  .person__name { font-weight: 700; font-size: 21px; line-height: 1.3; }
  .person__first { color: var(--brand-orange); }
  .person__last { color: var(--brand-green); }
  .person__title { color: var(--text-light); font-size: 13px; margin-top: 2px; }

  .divider {
    position: absolute;
    left: 276px; top: 112px;
    width: 1.5px; height: 104px;
    background: var(--text-light);
  }

  .contacts { position: absolute; left: 292px; top: 114px; list-style: none; }
  .contacts__item {
    display: flex; align-items: center; gap: 8px;
    color: var(--text-light); font-size: 13px; line-height: 20px;
    white-space: nowrap;
  }
  .contacts__icon { width: 13px; height: 13px; flex: none; }

  .back-band {
    position: absolute; left: 0; right: 0; bottom: 0;
    height: 58px; background: var(--brand-orange);
    border-top: 5px solid var(--brand-green);
    box-shadow: 0 -5px 0 var(--card-base);
  }
</style>
</head>
<body>

<section class="card card--front" aria-label="Business card front">
  <svg class="card__swoosh" viewBox="0 0 540 310" preserveAspectRatio="none" aria-hidden="true">
    <path d="M0,90 C40,170 150,270 400,310 L0,310 Z" fill="var(--brand-orange)"/>
    <path d="M28,86 C70,170 190,262 400,302" fill="none" stroke="var(--brand-green)" stroke-width="3"/>
  </svg>

  <div class="wordmark">Brightfen</div>

  <div class="person">
    <p class="person__name"><span class="person__first">Marta</span> <span class="person__last">Kovalska</span></p>
    <p class="person__title">Managing Director</p>
  </div>

  <span class="divider"></span>

  <ul class="contacts">
    <li class="contacts__item">
      <svg class="contacts__icon" viewBox="0 0 16 16" aria-hidden="true"><path d="M3 1h3l1.5 4-2 1.2a9 9 0 0 0 4.3 4.3L11 8.5l4 1.5v3a2 2 0 0 1-2 2A12 12 0 0 1 1 3a2 2 0 0 1 2-2z" fill="var(--brand-orange)"/></svg>
      (555) 214-3096
    </li>
    <li class="contacts__item">
      <svg class="contacts__icon" viewBox="0 0 16 16" aria-hidden="true"><rect x="2" y="6" width="12" height="8" rx="1.5" fill="var(--brand-orange)"/><path d="M1 6c2-4 12-4 14 0v1h-4V5.5H5V7H1z" fill="var(--brand-orange)"/></svg>
      (555) 214-3097
    </li>
    <li class="contacts__item">
      <svg class="contacts__icon" viewBox="0 0 16 16" aria-hidden="true"><rect x="1" y="3" width="14" height="10" rx="1" fill="var(--brand-orange)"/><path d="M1.5 3.5 8 9l6.5-5.5" fill="none" stroke="var(--card-base)" stroke-width="1.3"/></svg>
      info@brightfen.com
    </li>
    <li class="contacts__item">
      <svg class="contacts__icon" viewBox="0 0 16 16" aria-hidden="true"><circle cx="8" cy="8" r="7" fill="var(--brand-orange)"/><path d="M1 8h14M8 1c-3 3-3 11 0 14M8 1c3 3 3 11 0 14" fill="none" stroke="var(--card-base)" stroke-width="1"/></svg>
      www.brightfen.com
    </li>
    <li class="contacts__item">
      <svg class="contacts__icon" viewBox="0 0 16 16" aria-hidden="true"><path d="M8 1a5 5 0 0 0-5 5c0 4 5 9 5 9s5-5 5-9a5 5 0 0 0-5-5z" fill="var(--brand-orange)"/><circle cx="8" cy="6" r="2" fill="var(--card-base)"/></svg>
      1420 Fenmoor Rd, Austin, TX 78701
    </li>
  </ul>
</section>

<section class="card card--back" aria-label="Business card back">
  <div class="wordmark">Brightfen</div>
  <div class="back-band"></div>
</section>

</body>
</html>
```